Flat bootstrap design for existing site

I'm looking for a modern flat design based around an existing logo. This has to be a custom design (no external templates), and implemented into a bootstrap framework.

The logo is attached as 2 versions - choose whichever you want, that flows better with whatever design you choose.

Added screenshots of the existing site (currently using the default bootstrap layouts). Please make your designs around those pages in the screenshots (i.e. the homepage only has the postal code input and the header). The active page has 3 screenshots, because I wanted to illustrate the other states that would be visible (in the table rows).

This is a moving/junk removal website, just for some context.

Here's some example websites (flat designs) that I like, just to give you an idea of what I'm after.

https://www.plimvora.com/
https://dacklow.com/
https://trevanu.com/
https://quobrintal.com/en/

Coding

Coded - Design and coding required

Number of Pages Required

5+ page

Colors

Designer to choose colors to be used in the design.

Requirements
Must have
• It must be a modern/simple flat design, that is built around the existing logo (attached).
• It has to be implemented using bootstrap.

```html
<!DOCTYPE html>
<html lang="en">
<head>
<meta charset="utf-8">
<title>Haulvex — Junk Removal</title>
<link rel="stylesheet" href="https://fonts.googleapis.com/css2?family=Open+Sans:wght@300;400;700&family=Montserrat:wght@400;500&display=swap">
<style>
  :root {
    --accent: #48c8f0;
    --ink: #111111;
    --page-bg: #eaeaec;
    --header-bg: #ffffff;
    --field-border: #cccccc;
    --white: #ffffff;
  }
  * { box-sizing: border-box; margin: 0; padding: 0; }
  html, body {
    width: 1200px;
    height: 720px;
    overflow: hidden;
  }
  body {
    position: relative;
    background: var(--page-bg);
    color: var(--ink);
    font-family: "Open Sans", Arial, sans-serif;
  }
  .site-header {
    position: absolute;
    top: 0; left: 0;
    width: 1200px;
    height: 85px;
    background: var(--header-bg);
    box-shadow: 0 4px 14px rgba(0, 0, 0, 0.06);
  }
  .brand {
    position: absolute;
    left: 131px;
    top: 22px;
    font-family: "Open Sans", Arial, sans-serif;
    font-weight: 700;
    font-size: 30px;
    line-height: 40px;
    letter-spacing: 1px;
    color: var(--accent);
    text-decoration: none;
  }
  .main-nav {
    position: absolute;
    top: 26px;
    left: 0;
    width: 1200px;
    height: 29px;
    font-family: "Montserrat", Arial, sans-serif;
    font-size: 11px;
    letter-spacing: 0.2px;
  }
  .nav-link {
    position: absolute;
    top: 0;
    line-height: 29px;
    color: var(--ink);
    text-decoration: none;
  }
  .nav-book { left: 718px; }
  .nav-how { left: 778px; }
  .nav-driver {
    left: 886px;
    width: 126px;
    height: 29px;
    text-align: center;
    color: var(--accent);
    border: 1px solid var(--accent);
  }
  .nav-signin { left: 1031px; }
  .hero-title {
    position: absolute;
    top: 254px;
    left: 0;
    width: 1198px;
    text-align: center;
    font-weight: 300;
    font-size: 40px;
    line-height: 56px;
  }
  .postal-form {
    position: absolute;
    left: 276px;
    top: 367px;
    width: 648px;
    height: 79px;
    background: var(--white);
    border: 2px solid var(--field-border);
  }
  .postal-pin {
    position: absolute;
    left: 28px;
    top: 30px;
  }
  .postal-label {
    position: absolute;
    left: 54px;
    top: 0;
    line-height: 75px;
    font-family: "Montserrat", Arial, sans-serif;
    font-size: 12px;
    color: var(--ink);
  }
  .book-button {
    position: absolute;
    left: 515px;
    top: 15px;
    width: 113px;
    height: 45px;
    border: none;
    background: var(--accent);
    color: var(--white);
    font-family: "Open Sans", Arial, sans-serif;
    font-weight: 700;
    font-size: 18px;
    letter-spacing: 0.5px;
  }
</style>
</head>
<body>
  <header class="site-header">
    <a class="brand" href="#">HAULVEX</a>
    <nav class="main-nav">
      <a class="nav-link nav-book" href="#">BOOK</a>
      <a class="nav-link nav-how" href="#">HOW IT WORKS</a>
      <a class="nav-link nav-driver" href="#">BECOME A DRIVER</a>
      <a class="nav-link nav-signin" href="#">SIGN IN</a>
    </nav>
  </header>

  <main>
    <h1 class="hero-title">Need junk removed? Book Now</h1>
    <form class="postal-form">
      <svg class="postal-pin" width="12" height="16" viewBox="0 0 12 16" aria-hidden="true">
        <path d="M6 0C2.7 0 0 2.6 0 5.9 0 10.3 6 16 6 16s6-5.7 6-10.1C12 2.6 9.3 0 6 0zm0 8.3a2.4 2.4 0 1 1 0-4.8 2.4 2.4 0 0 1 0 4.8z" fill="#111"/>
      </svg>
      <span class="postal-label">POSTAL CODE</span>
      <button class="book-button" type="button">BOOK</button>
    </form>
  </main>
</body>
</html>
```